Maplecrest Disability - Social Security Disability Attorneys

Our company is expanding to attract clients nationwide for our social security disability practice. We have a logo, but I am looking for a creative and elegant letterhead that projects an image of being technologically advanced but still professional enough for the legal field. I am looking for the "wow factor" combined with this is still professional enough for a law practice.

Requesting letterhead and business card design
Updates

Had to update and change the logo. The previous logo had a typo. Please send updates with the new logo for consideration. The letterhead and business cards should be professional enough to be used for a law firm. Thanks.

Industry/Entity Type

Law Practice, Law Firm, Healthcare Industry, Government

Colors

Designer to choose colors to be used in the design.

Requirements
Nice to have
• **Please create a vertical design for the business card**

```html
<!DOCTYPE html>
<html lang="en">
<head>
<meta charset="utf-8">
<title>Maplecrest Disability – Business Card</title>
<link href="https://fonts.googleapis.com/css2?family=Montserrat:wght@400;500;600;700&display=swap" rel="stylesheet">
<style>
  :root {
    --stage: #219ed9;
    --brand-blue: #536fb7;
    --brand-orange: #f58a2c;
    --ink: #1a1a1a;
    --paper: #ffffff;
  }
  * { margin: 0; padding: 0; box-sizing: border-box; }
  html, body { width: 1200px; height: 1128px; overflow: hidden; }
  body {
    background: var(--stage);
    font-family: "Montserrat", Arial, sans-serif;
    position: relative;
  }
  .card {
    position: absolute;
    top: 129px;
    height: 868px;
    border-radius: 42px;
    overflow: hidden;
    box-shadow: 0 14px 34px rgba(0, 0, 0, 0.45);
    text-align: center;
  }
  .card--front { left: 70px; width: 500px; background: var(--paper); }
  .card--back { left: 633px; width: 496px; background: var(--brand-blue); color: var(--paper); }

  .brand { position: absolute; left: 0; right: 0; }
  .brand__dot {
    display: block;
    width: 28px; height: 28px;
    margin: 0 auto;
    border-radius: 50%;
    background: var(--brand-orange);
  }
  .brand__name {
    margin-top: 20px;
    font-size: 27px;
    font-weight: 600;
    letter-spacing: 1px;
    line-height: 1;
    color: var(--brand-blue);
  }
  .brand__tagline {
    margin-top: 9px;
    font-size: 9.5px;
    font-weight: 500;
    letter-spacing: 2.9px;
    text-transform: uppercase;
    color: var(--brand-blue);
  }
  .card--front .brand { top: 132px; }
  .card--back .brand { top: 154px; }
  .card--back .brand__dot { background: var(--paper); width: 24px; height: 24px; }
  .card--back .brand__name { font-size: 23px; margin-top: 18px; color: var(--paper); }
  .card--back .brand__tagline { font-size: 8px; letter-spacing: 2.5px; margin-top: 8px; color: var(--paper); }

  .person { position: absolute; top: 312px; left: 0; right: 0; }
  .person__name {
    font-size: 31px;
    font-weight: 700;
    color: var(--brand-orange);
    line-height: 1;
  }
  .person__role {
    display: flex;
    align-items: center;
    justify-content: center;
    gap: 6px;
    margin-top: 8px;
    font-size: 22px;
    font-weight: 500;
    color: var(--ink);
  }
  .person__role::before,
  .person__role::after {
    content: "";
    width: 66px; height: 2px;
    background: var(--brand-orange);
  }

  .address {
    position: absolute; top: 446px; left: 0; right: 0;
    font-size: 20px;
    font-weight: 500;
    line-height: 28px;
    color: var(--ink);
  }
  .contact-icons {
    position: absolute; top: 544px; left: 0; right: 0;
    display: flex; justify-content: center; gap: 38px;
  }
  .contact-icons svg { width: 22px; height: 22px; fill: var(--brand-orange); }
  .contact-list {
    position: absolute; top: 604px; left: 0; right: 0;
    list-style: none;
    font-size: 20px;
    font-weight: 500;
    line-height: 33px;
    color: var(--ink);
  }
  .card__wave { position: absolute; left: 0; bottom: 0; width: 500px; height: 868px; }

  .sectors {
    position: absolute; top: 738px; left: 0; right: 0;
    font-size: 20px;
    font-weight: 500;
    line-height: 29px;
  }
</style>
</head>
<body>

  <section class="card card--front" aria-label="Business card front">
    <svg class="card__wave" viewBox="0 0 500 868" aria-hidden="true">
      <path d="M0 805 C 40 818, 80 832, 120 832 C 200 830, 270 792, 340 790 C 410 789, 460 804, 500 818 L 500 868 L 0 868 Z" fill="var(--brand-blue)"/>
      <path d="M8 800 C 50 814, 85 822, 120 822 C 200 820, 270 774, 345 773 C 400 772, 445 788, 480 806 C 440 794, 400 786, 345 786 C 270 787, 200 822, 120 828 C 80 829, 40 815, 8 800 Z" fill="var(--brand-orange)"/>
    </svg>

    <div class="brand">
      <span class="brand__dot"></span>
      <div class="brand__name">MAPLECREST DISABILITY</div>
      <div class="brand__tagline">Social Security Disability Attorneys</div>
    </div>

    <div class="person">
      <div class="person__name">DALTON REEVES</div>
      <div class="person__role">Co-Founder</div>
    </div>

    <p class="address">Suite 4, Level 12, Harbour<br>Street Sydney NSW 2000</p>

    <div class="contact-icons" aria-hidden="true">
      <svg viewBox="0 0 24 24"><path d="M6.6 10.8a15.1 15.1 0 0 0 6.6 6.6l2.2-2.2a1 1 0 0 1 1-.25 11.4 11.4 0 0 0 3.6.57 1 1 0 0 1 1 1V20a1 1 0 0 1-1 1A17 17 0 0 1 3 4a1 1 0 0 1 1-1h3.5a1 1 0 0 1 1 1c0 1.25.2 2.45.57 3.57a1 1 0 0 1-.25 1z"/></svg>
      <svg viewBox="0 0 24 24"><path d="M2 5h20v14H2z M2 5l10 8 10-8" stroke="var(--paper)" stroke-width="1.4"/></svg>
      <svg viewBox="0 0 24 24"><circle cx="12" cy="12" r="10"/><path d="M2 12h20M12 2c3 3 3 17 0 20M12 2c-3 3-3 17 0 20" stroke="var(--paper)" stroke-width="1.2" fill="none"/></svg>
    </div>

    <ul class="contact-list">
      <li>555-214-7390</li>
      <li>info@maplecrestdisability.com</li>
      <li>www.maplecrestdisability.com</li>
    </ul>
  </section>

  <section class="card card--back" aria-label="Business card back">
    <div class="brand">
      <span class="brand__dot"></span>
      <div class="brand__name">MAPLECREST DISABILITY</div>
      <div class="brand__tagline">Social Security Disability Attorneys</div>
    </div>
    <p class="sectors">Law Practice, Law Firm,<br>Healthcare Industry, Government</p>
  </section>

</body>
</html>
```